Etiketten für junge Imkerei
Renate hat super schnell verstanden was ich mir vorstelle und auch Änderungen rasant umgesetzt. Ich werde in Zukunft auf jedenfall wieder mit Renate arbeiten.
Zielgruppe
Wir sind eine junge Imkerei, die spezielle und außergewöhnliche Honigspezialitäten vermarktet.
Ich verkaufe meine Produkte hauptsächlich auf dem Markt im direkten Kundenkontakt, dennoch wird ein Barcode benötigt da einige Produkte auch im Laden verfügbar sind. Meine Kunden sind hauptsächlich Frauen im mittleren Alter.
Heute brauche ich Etiketten für meine neuen OXYMEL (Sauerhonig) Produkte, Oxymel ist ein Arzneisaft der bereits in der Antike verwendet wurde:
- Amber Meadow (Blütenhonig, Apfelessig, Zitrone, Ingwer und Kurkuma)
- Storm Tonic (Apfelessig, Blütenhonig, Zwiebel, Ingwer, Meerrettich, Knoblauch, Senf, Zimt, Gewürznelken, Chilli, Blutorange)
- Kids (Blütenhonig, Apfelessig, Hagebutte, Holunderblüte)
Aufgabenstellung
Es soll ein Flaschenetikett werden.
Die Etikettengröße soll ungefähr 40x120 mm sein, wobei ich hier nicht auf eine genaue Rechteckige Form festgelegt bin, sondern auch gerne eine freie Form (z.B. Logo außerhalb). Dann bis max. 60mm hoch. Ich verwende die Flasche Vanta von Plumosa.
Inhalt: 200 ml.
Verwendetes Papier: Baumwollpapier
Barcode
Das Etikett soll vom Schema zu meinen anderen Etiketten passen. Es soll feminin und ein wenig verspielt sein aber edel wirken.
Es soll die Natürlichkeit wiederspiegeln aber nicht nach Arznei aussehen.
Im Anhang befinden sich 2 von meinen aktuellen Etiketten der Honige, diese werden auf Biofolie gedruckt.

```html
<!DOCTYPE html>
<html lang="de">
<head>
<meta charset="utf-8">
<title>Oxymel Amber Meadow – Flaschenetikett</title>
<link href="https://fonts.googleapis.com/css2?family=Baloo+2:wght@500;600;700;800&family=Passion+One:wght@700&display=swap" rel="stylesheet">
<style>
  :root {
    --frame-magenta: #e5007d;
    --ink: #111111;
    --brand-brown: #6b4a2e;
    --honey-light: #f8ad2a;
    --honey-deep: #f39200;
    --jar-top: #f7b733;
    --jar-bottom: #f08a1c;
    --barcode-green: #8fc793;
    --paper: #ffffff;
  }
  * { margin: 0; padding: 0; box-sizing: border-box; }
  html, body {
    width: 1200px;
    height: 3124px;
    overflow: hidden;
    background: var(--paper);
  }
  .label {
    position: relative;
    width: 1200px;
    height: 3124px;
    font-family: "Baloo 2", "Arial Rounded MT Bold", sans-serif;
  }
  .label-frame {
    position: absolute;
    inset: 0;
  }
  .brand-dot {
    position: absolute;
    left: 520px;
    top: 400px;
    width: 160px;
    height: 160px;
    border-radius: 50%;
    background: var(--honey-light);
  }
  .brand-name {
    position: absolute;
    left: 0;
    width: 1200px;
    top: 660px;
    text-align: center;
    font-size: 88px;
    font-weight: 600;
    line-height: 1;
    color: var(--brand-brown);
    letter-spacing: 2px;
  }
  .product-type {
    position: absolute;
    left: 0;
    width: 1200px;
    top: 890px;
    text-align: center;
    font-family: "Passion One", "Arial Black", sans-serif;
    font-weight: 700;
    font-size: 220px;
    line-height: 1;
    color: var(--ink);
    letter-spacing: 6px;
  }
  .product-visual {
    position: absolute;
    left: 330px;
    top: 1210px;
    width: 560px;
    height: 600px;
    border-radius: 46% 46% 40% 40%;
    background: radial-gradient(circle at 45% 55%, var(--jar-top), var(--jar-bottom) 75%);
  }
  .product-name {
    position: absolute;
    left: 0;
    width: 1200px;
    top: 1855px;
    text-align: center;
    font-size: 116px;
    line-height: 1;
    letter-spacing: -2px;
  }
  .product-name .light { color: var(--honey-light); font-weight: 500; }
  .product-name .bold { color: var(--honey-deep); font-weight: 800; }
  .contents-heading {
    position: absolute;
    left: 0;
    width: 1200px;
    top: 2080px;
    text-align: center;
    font-size: 52px;
    font-weight: 700;
    line-height: 1;
    color: var(--honey-deep);
  }
  .ingredients {
    position: absolute;
    left: 0;
    width: 1200px;
    top: 2160px;
    text-align: center;
    font-size: 40px;
    font-weight: 600;
    line-height: 60px;
    color: var(--ink);
  }
  .volume {
    position: absolute;
    right: 180px;
    top: 2410px;
    font-size: 68px;
    font-weight: 700;
    line-height: 1;
    color: var(--honey-deep);
  }
  .barcode-area {
    position: absolute;
    left: 180px;
    top: 2540px;
    width: 840px;
    height: 320px;
    background: var(--barcode-green);
    display: flex;
    align-items: center;
    justify-content: center;
    font-size: 50px;
    font-weight: 500;
    color: var(--ink);
  }
</style>
</head>
<body>
  <main class="label">
    <svg class="label-frame" width="1200" height="3124" viewBox="0 0 1200 3124" aria-hidden="true">
      <path d="M112,620 Q112,540 192,540 L300,540 Q340,540 340,500 L340,480 A260,260 0 0 1 860,480 L860,500 Q860,540 900,540 L1008,540 Q1088,540 1088,620 L1088,2920 Q1088,3000 1008,3000 L192,3000 Q112,3000 112,2920 Z"
            fill="none" stroke="var(--frame-magenta)" stroke-width="8"/>
    </svg>

    <div class="brand-dot" aria-hidden="true"></div>
    <div class="brand-name">Wabenzauber</div>

    <h1 class="product-type">OXYMEL</h1>

    <div class="product-visual" role="img" aria-label="Illustration: Honigglas mit Honiglöffel, von einem Bogen umrahmt"></div>

    <h2 class="product-name"><span class="light">AMBER</span><span class="bold">MEADOW</span></h2>

    <p class="contents-heading">Inhalt</p>
    <p class="ingredients">Blütenhonig, Apfelessig, Zitrone,<br>Ingwer &amp; Kurkuma</p>

    <p class="volume">200 ml</p>

    <div class="barcode-area">Platzhalter für Barcode</div>
  </main>
</body>
</html>
```